A start-up named "lumerova" - a clinical research organization needs a new PowerPoint design

We need a new PowerPoint Design (incl. business card and stationery design) for an early-stage start-up named "lumerova" seeking to build an ecosystem/ strategic partner alliances or consortium of committed and active collaborators to guide important components of the clinical trial.

Our ultimate goal is to avoid false neutrals – therapies that have not been and may never be evaluated in clinical trials due to the costs and/ or complexity.

The final design should highlight our patient-centric approach, innovative study design supported with the novel AI platform to make a stronger impact on patient lives.

Please see the attached brief for more details.
Updates

Requesting the proposals on color-coding, business-card designs, clinical research visuals, and icons as well as stationery design.

Target Market(s)

Pharma/ Biotech Executives
Medical Institutions
Clinical Trial Participants (Patients)

Colors
e34398

Requirements
Must have
• Use the Color Version of purple/ magenta logo

```html
<!DOCTYPE html>
<html lang="en">
<head>
<meta charset="utf-8">
<title>lumerova – presentation system</title>
<link href="https://fonts.googleapis.com/css2?family=Montserrat:wght@300;400;500;600;700&display=swap" rel="stylesheet">
<style>
:root{
  --magenta:#e0117f;
  --pink:#f06aa8;
  --plum:#a3165f;
  --teal-light:#8ecfc9;
  --teal:#1fa5a0;
  --green:#14997a;
  --ink:#1b1b1b;
  --grey:#8a8a8a;
  --paper:#ffffff;
  --canvas:#e9e9ec;
}
*{margin:0;padding:0;box-sizing:border-box}
html,body{width:1200px;height:3729px;overflow:hidden}
body{background:var(--canvas);font-family:"Montserrat",Arial,sans-serif;color:var(--ink);position:relative}
.slide{position:absolute;width:578px;height:326px;overflow:hidden;background:var(--paper);box-shadow:0 1px 4px rgba(0,0,0,.22)}
.c1{left:15px}.c2{left:605px}
.brand{position:absolute;font-weight:700;color:var(--magenta);font-size:13px;letter-spacing:-.2px;display:flex;align-items:center;gap:3px}
.brand::after{content:"";width:7px;height:7px;background:currentColor;display:block}
.brand.sm{top:12px;right:14px;font-size:11px}
.brand.white{color:#fff}
.foot{position:absolute;left:12px;bottom:6px;font-size:5px;color:var(--grey);letter-spacing:.2px}
.foot b{color:var(--magenta)}
.pg{position:absolute;right:0;bottom:0;width:14px;height:12px;background:var(--magenta);color:#fff;font-size:6px;line-height:12px;text-align:center}
.photo{position:absolute}
.stitle{position:absolute;left:28px;top:14px;font-size:17px;font-weight:500;color:var(--ink)}
.stitle::before{content:"";position:absolute;left:-22px;top:3px;width:8px;height:14px;background:var(--magenta)}
.pill{position:absolute;border-radius:10px;background:linear-gradient(90deg,var(--teal-light),var(--teal) 60%,var(--green));color:#fff;text-align:center;box-shadow:0 3px 8px rgba(0,0,0,.2)}
.pill .l1{font-weight:600;font-size:28px;line-height:30px}
.pill .l2{font-weight:300;font-size:28px;line-height:28px}
.big-title{position:absolute;font-weight:600;line-height:1.25}
.stats-panel{position:absolute;left:365px;top:0;width:213px;height:326px;color:#fff}
.stat-badge{position:absolute;left:-30px;width:34px;height:24px;background:#fff;border-radius:3px;color:var(--ink);font-size:17px;font-weight:600;text-align:center;line-height:24px;box-shadow:0 1px 3px rgba(0,0,0,.25)}
.stat-badge::before{content:"%";position:absolute;left:-8px;top:-10px;width:16px;height:16px;border-radius:50%;background:var(--pink);color:#fff;font-size:8px;line-height:16px}
.stat-text{position:absolute;left:38px;right:14px;font-size:8px;line-height:11px}
.stat-foot{position:absolute;left:20px;right:14px;bottom:18px;font-size:12px;font-weight:500;line-height:15px}
.tiny{font-size:5px;line-height:7px;color:#555}
.grid-tile{display:block;height:16px;border-radius:3px;background:#e2e2e6}
.tile-grid{position:absolute;display:grid;gap:14px 12px}
.tile-grid .grid-tile{width:100%}
table.dmu{position:absolute;left:28px;top:110px;width:522px;border-collapse:separate;border-spacing:0;box-shadow:0 2px 6px rgba(0,0,0,.15)}
table.dmu th{color:#fff;font-size:12px;font-weight:600;height:34px}
table.dmu td{font-size:9px;height:80px;padding:0 16px;vertical-align:middle;color:#555}
.col4{position:absolute;top:50px;width:125px;height:260px;border-radius:4px;color:#fff;text-align:center}
.col4 .tag{margin:12px auto 0;width:105px;height:20px;border-radius:10px;background:#222;font-size:6px;font-weight:700;line-height:20px}
.col4 .num{margin:20px auto 0;width:70px;height:70px;border-radius:50%;background:rgba(255,255,255,.35);border:5px solid rgba(255,255,255,.5);font-size:32px;font-weight:600;line-height:60px;color:#222}
.col4 .head{margin-top:20px;font-size:8px;font-weight:600;line-height:10px;padding:0 10px}
.col4 .body{margin-top:10px;font-size:6px;line-height:8px;padding:0 12px;opacity:.85}
.contact{position:absolute;bottom:58px;left:0;width:100%;display:flex;justify-content:space-around;padding:0 50px;font-size:5px;color:#fff}
.contact span::before{content:"";display:inline-block;width:6px;height:6px;border-radius:50%;background:var(--magenta);margin-right:4px;vertical-align:middle}
.swatch{position:absolute;top:162px;width:64px;height:64px;border-radius:50%}
.swatch-label{position:absolute;top:136px;font-size:12px;font-weight:600;text-align:center;width:64px}
.cro-list{position:absolute;left:310px;top:32px;width:260px;display:grid;grid-template-columns:24px 58px 1fr;align-items:center;font-size:5.5px;font-weight:600;line-height:28px}
.cro-list .grid-tile{width:50px}
</style>
</head>
<body>

<!-- 1 cover -->
<section class="slide c1" style="top:15px">
  <svg class="photo" role="img" aria-label="Photo of a doctor holding a stethoscope" width="578" height="326" style="left:0;top:0">
    <defs><linearGradient id="ph1" x1="0" y1="0" x2="1" y2="1"><stop offset="0" stop-color="#f1eaee"/><stop offset="1" stop-color="#cfc4c8"/></linearGradient></defs>
    <polygon points="330,0 578,0 578,326 200,326" fill="url(#ph1)"/>
    <polygon points="300,0 578,0 578,170" fill="var(--magenta)" opacity=".85"/>
    <polygon points="330,326 578,120 578,326" fill="var(--teal)" opacity=".85"/>
  </svg>
  <div class="brand" style="left:42px;top:72px;font-size:20px">lumerova</div>
  <div class="big-title" style="left:42px;top:112px;font-size:22px;color:var(--ink)">Your Awesome<br>Presentation Title<br>Goes Here</div>
  <div style="position:absolute;left:43px;top:248px;width:122px;height:20px;border-radius:10px;background:var(--magenta);color:#fff;font-size:8px;text-align:center;line-height:20px">Date</div>
</section>

<!-- 2 cover pink -->
<section class="slide c2" style="top:15px">
  <div class="photo" role="img" aria-label="Magenta-tinted photo of a doctor holding a stethoscope" style="inset:0;background:linear-gradient(120deg,#f59cc6,#e8529b 60%,#d92a86)"></div>
  <div class="brand white" style="left:52px;top:70px;font-size:17px">lumerova</div>
  <div class="big-title" style="left:52px;top:132px;font-size:22px;color:#fff">Your Awesome<br>Presentation Title<br>Goes Here</div>
  <div class="pg" style="background:none;color:#fff">2</div>
</section>

<!-- 3 cover light -->
<section class="slide c1" style="top:352px">
  <div class="photo" role="img" aria-label="Photo of a doctor with crossed arms and translucent magenta squares" style="inset:0;background:linear-gradient(90deg,#f4f1f2,#e7dfe2 55%,#f3c3d9 80%,#ece8ea)"></div>
  <div class="brand" style="left:42px;top:150px;font-size:20px">lumerova</div>
  <div class="big-title" style="left:44px;top:200px;font-size:18px;color:var(--ink)">Your Awesome Presentation<br>Title Goes Here</div>
</section>

<!-- 4 challenge -->
<section class="slide c2" style="top:352px">
  <svg class="photo" role="img" aria-label="Photo of a scientist at a microscope" width="578" height="326" style="left:0;top:0">
    <defs><linearGradient id="ph4" x1="0" y1="0" x2="1" y2="0"><stop offset="0" stop-color="#e3e8ee"/><stop offset="1" stop-color="#9aa7b4"/></linearGradient></defs>
    <path d="M0,0 H420 C330,40 290,120 300,326 H0Z" fill="url(#ph4)"/>
    <path d="M420,0 C330,40 290,120 300,326 H318 C310,140 340,50 440,0Z" fill="var(--magenta)"/>
  </svg>
  <div class="brand sm">lumerova</div>
  <div class="pill" style="left:210px;top:187px;width:330px;height:92px;padding-top:14px"><div class="l1">Challenge/</div><div class="l2">unmet need</div></div>
  <div class="foot"><b>LUMEROVA</b> | Copyright © All Rights Reserved</div><div class="pg">4</div>
</section>

<!-- 5 drug development -->
<section class="slide c1" style="top:689px">
  <div class="stitle">New Drug Development Process</div>
  <div style="position:absolute;left:20px;top:42px;width:290px;height:260px;background:#fff;box-shadow:0 2px 8px rgba(0,0,0,.15)"></div>
  <svg width="578" height="326" style="position:absolute;left:0;top:0">
    <circle cx="128" cy="178" r="78" fill="#8d1355"/>
    <g stroke="#fff" stroke-width="3">
      <line x1="128" y1="178" x2="128" y2="100"/><line x1="128" y1="178" x2="202" y2="154"/>
      <line x1="128" y1="178" x2="174" y2="241"/><line x1="128" y1="178" x2="82" y2="241"/>
      <line x1="128" y1="178" x2="54" y2="154"/>
    </g>
    <circle cx="128" cy="178" r="20" fill="#fff"/>
    <g fill="#fff" font-size="5" text-anchor="middle" font-family="Montserrat">
      <text x="158" y="130">DRUG DISCOVERY</text><text x="158" y="137">AND LAB RESEARCH</text>
      <text x="172" y="186">PRECLINICAL</text><text x="172" y="193">TESTING</text>
      <text x="128" y="228">CLINICAL TRIALS</text><text x="128" y="235">Phases I, II, III</text>
      <text x="84" y="186">POSTMARKETING</text><text x="84" y="193">1 approved drug</text>
      <text x="95" y="138">COMMERCIALIZATION</text>
    </g>
    <g fill="#555" font-size="4.5" font-family="Montserrat"><text x="50" y="80">FDA approval</text><text x="40" y="275">New drug application</text><text x="215" y="268">Investigational new</text><text x="215" y="274">drug application</text></g>
  </svg>
  <div class="stats-panel" style="background:linear-gradient(135deg,#e3378f,var(--plum))">
    <div class="stat-badge" style="top:56px">70</div><div class="stat-text" style="top:50px">70% of potencial participants &gt; 2 hrs away from the closests clinical trail site/ study center</div>
    <div class="stat-badge" style="top:110px">67</div><div class="stat-text" style="top:108px">67% of sites fail to meet enrolment goals</div>
    <div class="stat-badge" style="top:164px">30</div><div class="stat-text" style="top:170px">30% average drop out rate</div>
    <svg width="30" height="14" style="position:absolute;left:90px;top:226px"><polygon points="0,0 30,0 15,14" fill="#3a0a22"/></svg>
    <div class="stat-foot">85% of clinical trails fail to retain enough patients</div>
  </div>
  <div class="foot"><b>LUMEROVA</b> | Copyright © All Rights Reserved</div><div class="pg" style="background:none;color:#fff">5</div>
</section>

<!-- 6 drug development teal -->
<section class="slide c2" style="top:689px">
  <div class="stitle">New Drug Development Process</div>
  <svg width="578" height="326" style="position:absolute;left:0;top:0">
    <circle cx="128" cy="178" r="80" fill="var(--teal)"/>
    <path d="M128,178 L128,98 A80,80 0 0 1 204,153Z" fill="#d81b7e"/>
    <path d="M128,178 L204,153 A80,80 0 0 1 175,243Z" fill="#e54a98"/>
    <path d="M128,178 L175,243 A80,80 0 0 1 81,243Z" fill="#f27cb5"/>
    <path d="M128,178 L81,243 A80,80 0 0 1 52,153Z" fill="#f59cc6"/>
    <path d="M128,178 L52,153 A80,80 0 0 1 128,98Z" fill="#fff"/>
    <circle cx="128" cy="178" r="64" fill="none" stroke="var(--teal)" stroke-width="4"/>
    <circle cx="128" cy="178" r="20" fill="#fff"/>
    <g fill="#fff" font-size="5" text-anchor="middle" font-family="Montserrat">
      <text x="158" y="130">DRUG DISCOVERY</text><text x="158" y="137">AND LAB RESEARCH</text>
      <text x="172" y="186">PRECLINICAL</text><text x="172" y="193">TESTING</text>
      <text x="128" y="228">CLINICAL TRIALS</text><text x="128" y="235">Phases I, II, III</text>
      <text x="84" y="186">POSTMARKETING</text><text x="84" y="193">1 approved drug</text>
    </g>
    <text x="95" y="138" font-size="5" fill="var(--teal)" text-anchor="middle" font-family="Montserrat">COMMERCIALIZATION</text>
    <g fill="#555" font-size="4.5" font-family="Montserrat"><text x="40" y="80">FDA approval</text><text x="30" y="275">New drug application</text><text x="215" y="268">Investigational new</text><text x="215" y="274">drug application</text></g>
  </svg>
  <div class="stats-panel" style="background:linear-gradient(135deg,#1f6f61,#1d4d44)"></div>
  <div class="stats-panel" style="background:linear-gradient(200deg,rgba(31,111,97,0) 35%,#d9237f 80%)">
    <div class="stat-badge" style="top:56px;color:var(--teal)">70</div><div class="stat-text" style="top:50px">70% of potencial participants &gt; 2 hrs away from the closests clinical trail site/ study center</div>
    <div class="stat-badge" style="top:110px;color:var(--teal)">67</div><div class="stat-text" style="top:108px">67% of sites fail to meet enrolment goals</div>
    <div class="stat-badge" style="top:164px;color:var(--teal)">30</div><div class="stat-text" style="top:170px">30% average drop out rate</div>
    <svg width="30" height="14" style="position:absolute;left:90px;top:226px"><polygon points="0,0 30,0 15,14" fill="#3a0a22"/></svg>
    <div class="stat-foot">85% of clinical trails fail to retain enough patients</div>
  </div>
  <div class="foot"><b>LUMEROVA</b> | Copyright © All Rights Reserved</div><div class="pg" style="background:none;color:#fff">6</div>
</section>

<!-- 7 why don't patients enrol -->
<section class="slide c1" style="top:1026px">
  <div class="brand sm">lumerova</div>
  <div style="position:absolute;left:0;top:148px;width:14px;height:26px;background:var(--magenta)"></div>
  <div style="position:absolute;left:38px;top:118px;font-size:7px;color:var(--magenta);font-weight:600">TRUST.UNDERSTANDING.CONVENIENCE</div>
  <div class="big-title" style="left:38px;top:134px;font-size:24px;line-height:30px">Why don't<br>patients enrol<br>in trials?</div>
  <div style="position:absolute;left:242px;top:80px;width:10px;height:200px;font-size:5px;writing-mode:vertical-rl;transform:rotate(180deg);font-weight:600;text-align:center">Reasons for not enrolling in a clinical trial, share of patients</div>
  <div style="position:absolute;left:258px;top:80px;width:1px;height:200px;background:#333"></div>
  <div style="position:absolute;left:270px;top:56px;width:292px;height:30px;font-size:20px;font-weight:600">
    <span style="position:absolute;left:30px;color:var(--magenta)">67<small style="font-size:9px">%</small></span>
    <span style="position:absolute;left:130px;top:4px;color:#9b2b8a">66<small style="font-size:9px">%</small></span>
    <span style="position:absolute;left:225px;top:20px;color:var(--plum)">56<small style="font-size:9px">%</small></span>
  </div>
  <div style="position:absolute;left:270px;top:92px;width:80px;height:80px;background:linear-gradient(#f27cb5,var(--magenta));color:#fff;font-size:6px;text-align:center;padding-top:20px">Insufficient staff<br>time</div>
  <div style="position:absolute;left:368px;top:94px;width:80px;height:78px;background:linear-gradient(#b54fb0,#8b2e88);color:#fff;font-size:6px;text-align:center;padding-top:20px">Length and<br>complexity of<br>consent forms</div>
  <div style="position:absolute;left:466px;top:110px;width:80px;height:62px;background:linear-gradient(#c1307d,var(--plum));color:#fff;font-size:6px;text-align:center;padding-top:12px">Transportation<br>to trial visits</div>
  <div style="position:absolute;left:270px;top:172px;width:80px;height:106px;background:#e9e9ec"></div>
  <div style="position:absolute;left:368px;top:172px;width:80px;height:106px;background:#e9e9ec"></div>
  <div style="position:absolute;left:466px;top:172px;width:80px;height:106px;background:#e9e9ec"></div>
  <svg width="300" height="40" style="position:absolute;left:270px;top:225px" fill="none" stroke="#999" stroke-width="1.2">
    <circle cx="40" cy="12" r="5"/><path d="M32,32 v-10 h16 v10"/>
    <rect x="129" y="4" width="20" height="26" rx="2"/><line x1="134" y1="12" x2="144" y2="12"/><line x1="134" y1="18" x2="144" y2="18"/>
    <path d="M224,24 l6,-10 h22 l6,10 v6 h-34z"/><circle cx="232" cy="30" r="3"/><circle cx="250" cy="30" r="3"/>
  </svg>
  <div class="foot"><b>LUMEROVA</b> | Copyright © All Rights Reserved</div><div class="pg">7</div>
</section>

<!-- 8 AI solution -->
<section class="slide c2" style="top:1026px">
  <div class="stitle" style="line-height:22px">AI as a solution in clinical<br>trial analysis</div>
  <div style="position:absolute;left:20px;top:100px;width:280px;height:62px;border-radius:30px;background:#fff;box-shadow:0 2px 8px rgba(0,0,0,.15)"></div>
  <div class="stat-badge" style="left:28px;top:122px;color:var(--magenta)">80</div>
  <div style="position:absolute;left:80px;top:112px;font-size:11px;color:var(--magenta);font-weight:600">80% of the 350 respondents</div>
  <div style="position:absolute;left:80px;top:126px;font-size:6px;color:var(--magenta);line-height:8px">in biopharma report that they plan to use<br>AI or big data analytics within 5 years</div>
  <div style="position:absolute;left:20px;top:192px;width:280px;height:62px;border-radius:30px;background:#fff;box-shadow:0 2px 8px rgba(0,0,0,.15)"></div>
  <div class="stat-badge" style="left:28px;top:214px;color:var(--teal)">55</div>
  <div style="position:absolute;left:80px;top:204px;font-size:11px;color:var(--teal);font-weight:600">55% of the respondents said</div>
  <div style="position:absolute;left:80px;top:218px;font-size:6px;color:var(--magenta);line-height:8px">They were partnering with tech companies to help<br>expand data gathering/processing capacity</div>
  <div class="photo" role="img" aria-label="Magenta panel with faint technology and analytics imagery" style="left:365px;top:0;width:213px;height:326px;background:linear-gradient(160deg,#e64b9a,var(--plum))"></div>
  <div style="position:absolute;left:385px;top:32px;width:180px;color:#fff;font-size:9px;font-weight:600;text-align:center;line-height:12px">Top-three digital challenges<br>sponsors indentified</div>
  <div style="position:absolute;left:337px;top:90px;width:235px">
    <div style="position:absolute;left:0;top:0;width:22px;height:22px;border-radius:50%;background:#fff;font-size:8px;font-weight:600;text-align:center;line-height:22px;box-shadow:0 1px 3px rgba(0,0,0,.3)">01</div>
    <div style="position:absolute;left:48px;top:4px;color:#fff;font-size:7px;line-height:9px">Digital technology and AI to<br>improve clinical trial efficiency</div>
    <div style="position:absolute;left:0;top:70px;width:22px;height:22px;border-radius:50%;background:#fff;font-size:8px;font-weight:600;text-align:center;line-height:22px;box-shadow:0 1px 3px rgba(0,0,0,.3)">02</div>
    <div style="position:absolute;left:48px;top:77px;color:#fff;font-size:7px">Analyze complex data sets</div>
    <div style="position:absolute;left:0;top:140px;width:22px;height:22px;border-radius:50%;background:#fff;font-size:8px;font-weight:600;text-align:center;line-height:22px;box-shadow:0 1px 3px rgba(0,0,0,.3)">03</div>
    <div style="position:absolute;left:48px;top:144px;color:#fff;font-size:7px;line-height:9px">Integrate data from disparate<br>sources</div>
  </div>
  <div class="foot"><b>LUMEROVA</b> | Copyright © All Rights Reserved</div><div class="pg" style="background:none;color:#fff">8</div>
</section>

<!-- 9 organisation divider -->
<section class="slide c1" style="top:1363px">
  <svg class="photo" role="img" aria-label="Photo of a busy city street crowd" width="578" height="326" style="left:0;top:0">
    <defs><linearGradient id="ph9" x1="0" y1="0" x2="1" y2="1"><stop offset="0" stop-color="#5a6470"/><stop offset="1" stop-color="#2b3138"/></linearGradient></defs>
    <path d="M0,0 H370 C380,110 320,190 200,200 C120,205 60,220 0,240Z" fill="url(#ph9)"/>
    <path d="M370,0 C380,110 320,190 200,200 C120,205 60,220 0,240 V258 C60,236 130,222 210,216 C340,204 400,110 386,0Z" fill="var(--magenta)"/>
  </svg>
  <div class="brand sm">lumerova</div>
  <div class="pill" style="left:210px;top:187px;width:330px;height:92px;padding-top:14px"><div class="l1">Organisation &amp;</div><div class="l2">Target Audience</div></div>
  <div class="foot"><b>LUMEROVA</b> | Copyright © All Rights Reserved</div><div class="pg">9</div>
</section>

<!-- 10 organisation -->
<section class="slide c2" style="top:1363px">
  <div class="stitle">Organisation/ Who we are</div>
  <div class="brand sm">lumerova</div>
  <div style="position:absolute;left:60px;top:50px;width:460px;font-size:7.5px;text-align:center;line-height:10px;font-weight:600">LUMEROVA is an early-stage start-up seeking to <span style="color:var(--magenta)">build an ecosystem/strategic partner alliances</span> or consortium of committed and active collaborators to guide important components of the clinical trial.</div>
  <div style="position:absolute;left:0;top:236px;width:578px;height:90px;background:linear-gradient(90deg,var(--magenta),#d71f82)"></div>
  <div style="position:absolute;left:40px;top:110px;width:140px;height:150px;border-radius:30px 30px 0 0;background:#fff;box-shadow:0 -2px 8px rgba(0,0,0,.1);padding:28px 14px 0;text-align:center" class="tiny">The Science around new medical treatments is rapidly progressing, but there are many questions surrounding <span style="color:var(--pink)">how Science could translate into Therapy</span></div>
  <div style="position:absolute;left:219px;top:100px;width:140px;height:160px;border-radius:30px 30px 0 0;background:#fff;box-shadow:0 -2px 8px rgba(0,0,0,.1);padding:28px 14px 0;text-align:center" class="tiny">Success lies in moving from an idea generating phase at a 50,000-foot level to the on-the ground implementation phase. It is crucial to strike a balance between what is <span style="color:var(--pink)">scientifically valuable and operationally feasible</span></div>
  <div style="position:absolute;left:398px;top:110px;width:140px;height:150px;border-radius:30px 30px 0 0;background:#fff;box-shadow:0 -2px 8px rgba(0,0,0,.1);padding:28px 14px 0;text-align:center" class="tiny">We have no time or money to spend on wasted efforts. We really need to focus on tasks where our patients could gain something. We have to figure out how we can best use science at our disposal to avoid type 1 error but also <span style="color:var(--pink)">get superior treatments to patients</span></div>
  <div style="position:absolute;left:0;top:272px;width:578px;text-align:center;color:#fff;font-size:11px">...therefore, we strive to work with lumerova (for patients)</div>
  <div class="foot" style="color:#fff"><b style="color:#fff">LUMEROVA</b> | Copyright © All Rights Reserved</div><div class="pg" style="background:#fff;color:var(--magenta)">10</div>
</section>

<!-- 11 target audience cycle -->
<section class="slide c1" style="top:1700px">
  <div class="brand sm">lumerova</div>
  <div style="position:absolute;left:0;top:148px;width:14px;height:26px;background:var(--magenta)"></div>
  <div class="big-title" style="left:34px;top:142px;font-size:19px;line-height:24px;font-weight:500">Target<br>Audience</div>
  <svg width="578" height="326" style="position:absolute;left:0;top:0" font-family="Montserrat">
    <defs><marker id="ah" markerWidth="6" markerHeight="6" refX="3" refY="3" orient="auto"><path d="M0,0 L6,3 L0,6Z" fill="context-stroke"/></marker></defs>
    <path d="M240,105 A90,75 0 0 1 340,60" fill="none" stroke="var(--pink)" stroke-width="3" marker-end="url(#ah)"/>
    <path d="M405,60 A90,75 0 0 1 460,115" fill="none" stroke="var(--green)" stroke-width="3" marker-end="url(#ah)"/>
    <path d="M460,200 A90,75 0 0 1 405,255" fill="none" stroke="var(--magenta)" stroke-width="3" marker-end="url(#ah)"/>
    <path d="M340,255 A90,75 0 0 1 250,210" fill="none" stroke="var(--teal-light)" stroke-width="3" marker-end="url(#ah)"/>
    <line x1="303" y1="160" x2="430" y2="160" stroke="var(--magenta)" stroke-width="3"/>
    <g fill="#fff" stroke="#ddd"><rect x="348" y="42" width="48" height="48" rx="6"/><rect x="255" y="136" width="48" height="48" rx="6"/><rect x="430" y="136" width="48" height="48" rx="6"/><rect x="348" y="226" width="48" height="48" rx="6"/></g>
    <g fill="none" stroke="var(--pink)" stroke-width="1.5">
      <circle cx="372" cy="58" r="6"/><path d="M362,80 q10,-14 20,0"/>
      <path d="M272,150 h10 v10 l8,14 h-26 l8,-14z"/>
      <rect x="444" y="148" width="20" height="26"/><line x1="454" y1="152" x2="454" y2="160"/><line x1="450" y1="156" x2="458" y2="156"/>
    </g>
    <g fill="none" stroke="var(--teal-light)" stroke-width="1.5"><circle cx="372" cy="242" r="6"/><path d="M362,266 q10,-14 20,0"/></g>
    <text x="372" y="30" font-size="6" fill="var(--magenta)" text-anchor="middle" font-weight="600">Participants/ Patients</text>
    <text x="450" y="75" font-size="5" fill="#333">Implementation</text><text x="450" y="82" font-size="5" fill="#333">Of Clinical Trails</text>
    <text x="262" y="75" font-size="5" fill="#333" text-anchor="middle">Drug Candidates</text>
    <text x="368" y="154" font-size="9" fill="var(--magenta)" text-anchor="middle" font-weight="600">Request</text>
    <text x="220" y="157" font-size="5" fill="var(--pink)" text-anchor="middle">Pharmaceutical/</text><text x="220" y="164" font-size="5" fill="var(--pink)" text-anchor="middle">Biotech</text><text x="220" y="171" font-size="5" fill="var(--pink)" text-anchor="middle">Companies</text>
    <text x="483" y="157" font-size="5" fill="var(--magenta)">Medical</text><text x="483" y="164" font-size="5" fill="var(--magenta)">Institutions/</text><text x="483" y="171" font-size="5" fill="var(--magenta)">Hospitals</text>
    <text x="250" y="242" font-size="5" fill="#333" text-anchor="middle">CRO Services</text>
    <text x="455" y="250" font-size="5" fill="#333">SMO Services</text>
  </svg>
  <div class="brand" style="left:327px;top:293px;font-size:11px">lumerova</div>
  <div class="foot"><b>LUMEROVA</b> | Copyright © All Rights Reserved</div><div class="pg">11</div>
</section>

<!-- 12 decision makers -->
<section class="slide c2" style="top:1700px">
  <div class="stitle"><b style="font-weight:600">Target Audience:</b> Decision Makers</div>
  <div class="brand sm">lumerova</div>
  <div style="position:absolute;left:28px;top:80px;font-size:10px;font-weight:600">Based At The Pharma Companies; Highly Complex (One DMU for each drug)</div>
  <table class="dmu">
    <tr><th style="background:var(--magenta)">Economic Buyer</th><th style="background:var(--teal-light)">Influencer</th><th style="background:var(--plum)">Champion</th><th style="background:var(--teal)">Veto</th></tr>
    <tr>
      <td style="background:#f3f3f4">Global Program Leader</td>
      <td style="background:#eef7f6">• Clinical Operations Leader<br>• Header Development Operations</td>
      <td style="background:#fbeef4">• Medical Director<br>• R&amp;D Innovation/Digital Heads</td>
      <td style="background:#eaf4f4">Chief Financial Officer</td>
    </tr>
  </table>
  <div class="foot"><b>LUMEROVA</b> | Copyright © All Rights Reserved</div><div class="pg">12</div>
</section>

<!-- 13 fan -->
<section class="slide c1" style="top:2037px">
  <div class="brand sm">lumerova</div>
  <svg width="578" height="326" style="position:absolute;left:0;top:0" font-family="Montserrat">
    <g fill="#fff" stroke="#e6e6e6" filter="drop-shadow(0 2px 3px rgba(0,0,0,.12))">
      <path d="M285,225 L120,200 Q110,150 150,110 Z"/>
      <path d="M285,225 L160,100 Q200,55 260,55 Z"/>
      <path d="M285,225 L270,50 Q340,40 380,70 Z"/>
      <path d="M285,225 L390,80 Q440,110 450,150 Z"/>
      <path d="M285,225 L455,165 Q470,210 450,250 Z"/>
    </g>
    <g font-size="7" font-weight="600" text-anchor="middle">
      <text x="165" y="180" fill="var(--magenta)">lumen</text>
      <text x="205" y="110" fill="var(--magenta)">luminous</text>
      <text x="300" y="70" fill="var(--green)">lumina</text>
      <text x="390" y="115" fill="var(--teal)">lumière</text>
      <text x="420" y="200" fill="var(--teal)">luminance</text>
    </g>
    <g font-size="4.5" fill="#555" text-anchor="middle">
      <text x="165" y="188">light, or the unit</text><text x="165" y="194">measuring a flow</text><text x="165" y="200">of light</text>
      <text x="205" y="118">giving off bright</text><text x="205" y="124">light; clear and</text><text x="205" y="130">easy to grasp</text>
      <text x="300" y="78">a source of light</text><text x="300" y="84">or brightness</text>
      <text x="390" y="123">light, in the</text><text x="390" y="129">sense of insight</text>
      <text x="420" y="208">intensity of light</text><text x="420" y="214">given by a surface</text>
    </g>
  </svg>
  <div class="brand" style="left:240px;top:208px;font-size:18px">lumerova</div>
  <div style="position:absolute;left:0;top:248px;width:578px;text-align:center;font-size:8px;color:var(--magenta);font-weight:600;line-height:10px">Bringing Clear Insight And Discernment.<br>Brightly, Clearly, Openly, Acutely</div>
  <div style="position:absolute;left:67px;top:278px;width:444px;height:22px;border-radius:11px;background:var(--teal);color:#fff;font-size:11px;font-weight:600;text-align:center;line-height:22px">We strive to work with lumerova <span style="font-weight:400">(for patients)</span></div>
  <div class="foot"><b>LUMEROVA</b> | Copyright © All Rights Reserved</div><div class="pg">13</div>
</section>

<!-- 14 four columns -->
<section class="slide c2" style="top:2037px">
  <div class="brand sm">lumerova</div>
  <div class="col4" style="left:8px;background:linear-gradient(#f27cb5,#ec5ea2)"><div class="tag">DIFFERENT QUESTIONS</div><div class="num">01</div><div class="head">PATIENT CENTRIC/<br>THINK DISEASE</div><div class="body">When you think about a patient rather than a drug, there are obviously many questions related to drugs, treatments, combinations, etc. to be answered.</div></div>
  <div class="col4" style="left:148px;background:linear-gradient(#f06aa8,#e94b98)"><div class="tag">MORE ANSWERS</div><div class="num">02</div><div class="head">NEW TRIAL DESIGN/<br>MORE ANSWERS</div><div class="body">Ask and answer many questions about disease and disease population. Not seeking answers to outdated questions</div></div>
  <div class="col4" style="left:288px;background:linear-gradient(var(--magenta),#c80f72)"><div class="tag" style="line-height:9px;padding-top:1px">FASTER &amp; BETTER<br>INSIGHTS</div><div class="num">03</div><div class="head">DATA/ ARTIFICIAL<br>INTELLIGENCE (AI)</div><div class="body">Ability to quickly gather and use meaningful information</div></div>
  <div class="col4" style="left:428px;background:linear-gradient(#b31f6c,var(--plum))"><div class="tag">STRONGER IMPACT</div><div class="num">04</div><div class="head">SAVING LIVES/<br>MAKING IMPACT</div><div class="body">Avoid False neutrals – therapies that have not been and may never be evaluated in clinical trials</div></div>
  <div class="foot"><b>LUMEROVA</b> | Copyright © All Rights Reserved</div><div class="pg">14</div>
</section>

<!-- 15 market divider -->
<section class="slide c1" style="top:2374px">
  <svg class="photo" role="img" aria-label="Photo of a running track with lane markings" width="578" height="326" style="left:0;top:0">
    <defs><linearGradient id="ph15" x1="0" y1="0" x2="0" y2="1"><stop offset="0" stop-color="#c9ced4"/><stop offset="1" stop-color="#5f6770"/></linearGradient></defs>
    <path d="M578,0 H260 C230,60 150,100 0,110 V0Z" fill="#f4f4f4"/>
    <path d="M578,0 H290 C270,90 230,160 320,210 C420,240 520,240 578,220Z" fill="url(#ph15)"/>
    <path d="M290,0 C270,90 230,160 320,210 C420,240 520,240 578,220 V236 C520,256 410,256 310,222 C210,170 250,90 272,0Z" fill="var(--magenta)"/>
  </svg>
  <div class="pill" style="left:40px;top:187px;width:330px;height:92px;padding-top:14px"><div class="l1">MARKET</div><div class="l2">Competition</div></div>
  <div class="foot"><b>LUMEROVA</b> | Copyright © All Rights Reserved</div><div class="pg">15</div>
</section>

<!-- 16 top 10 CROs -->
<section class="slide c2" style="top:2374px">
  <div class="stitle" style="font-size:15px;line-height:18px"><b style="font-weight:600">Competition:</b> TOP 10 Clinical<br>Research Organizations (CROs)</div>
  <div class="brand sm" style="top:10px">lumerova</div>
  <svg width="300" height="326" style="position:absolute;left:0;top:0" font-family="Montserrat">
    <g transform="rotate(-90 130 175)" fill="none" stroke-width="60">
      <circle cx="130" cy="175" r="50" stroke="var(--pink)" stroke-dasharray="62.8 314.2"/>
      <circle cx="130" cy="175" r="50" stroke="var(--magenta)" stroke-dasharray="0 62.8 62.8 188.6"/>
      <circle cx="130" cy="175" r="50" stroke="var(--plum)" stroke-dasharray="0 125.6 62.8 125.8"/>
      <circle cx="130" cy="175" r="50" stroke="var(--teal-light)" stroke-dasharray="0 188.4 62.8 63"/>
      <circle cx="130" cy="175" r="50" stroke="var(--teal)" stroke-dasharray="0 251.2 62.8 0.2"/>
    </g>
    <circle cx="130" cy="175" r="28" fill="#fff"/>
    <g fill="#fff" font-size="6.5" text-anchor="middle">
      <text x="162" y="120">Investigator</text><text x="162" y="128">Networks</text>
      <text x="188" y="172">Clinical</text><text x="188" y="180">conduct &amp;</text><text x="188" y="188">Monitoring</text>
      <text x="150" y="232">Data Management</text><text x="150" y="240">&amp; Biostatistics</text>
      <text x="78" y="206">Consulting</text><text x="78" y="214">Auditing/</text><text x="78" y="222">Training</text>
      <text x="90" y="150">Regulatory</text>
    </g>
    <text x="130" y="278" font-size="7" text-anchor="middle" font-weight="600">CORE ACTIVITIES</text>
  </svg>
  <div class="brand" style="left:106px;top:168px;font-size:8px">lumerova</div>
  <div class="cro-list">
    <span>01</span><span class="grid-tile"></span><span>Northgate Biolab Corporation</span>
    <span>02</span><span class="grid-tile"></span><span>Halvern Clinical Holdings, Inc</span>
    <span>03</span><span class="grid-tile"></span><span>Brightmoor Health</span>
    <span>04</span><span class="grid-tile"></span><span>Tessaline International Corporation</span>
    <span>05</span><span class="grid-tile"></span><span>Orvanne Health Science</span>
    <span>06</span><span class="grid-tile"></span><span>Kestrel Trial Development (KTD)</span>
    <span>07</span><span class="grid-tile"></span><span>Ambergate Laboratories International (AGL)</span>
    <span>08</span><span class="grid-tile"></span><span>Fenwick Research Limited</span>
    <span>09</span><span class="grid-tile"></span><span>Dunmere Biotech</span>
    <span>10</span><span class="grid-tile"></span><span>Calloway Trials Holding, Inc</span>
  </div>
  <div class="foot"><b>LUMEROVA</b> | Copyright © All Rights Reserved</div><div class="pg">16</div>
</section>

<!-- 17 competition logos -->
<section class="slide c1" style="top:2711px">
  <div style="position:absolute;left:8px;top:12px;width:6px;height:12px;background:var(--magenta)"></div>
  <div style="position:absolute;left:24px;top:12px;font-size:13px;line-height:16px"><b style="font-weight:600">Competition Logos:</b><br>Clinical Research Organizations (CROs)</div>
  <div class="brand sm">lumerova</div>
  <div class="tile-grid" style="left:28px;top:62px;width:520px;grid-template-columns:repeat(8,1fr)">
    <span class="grid-tile"></span><span class="grid-tile"></span><span class="grid-tile"></span><span class="grid-tile"></span><span class="grid-tile"></span><span class="grid-tile"></span><span class="grid-tile"></span><span class="grid-tile"></span>
    <span class="grid-tile"></span><span class="grid-tile"></span><span class="grid-tile"></span><span class="grid-tile"></span><span class="grid-tile"></span><span class="grid-tile"></span><span class="grid-tile"></span><span class="grid-tile"></span>
    <span class="grid-tile"></span><span class="grid-tile"></span><span class="grid-tile"></span><span class="grid-tile"></span><span class="grid-tile"></span><span class="grid-tile"></span><span class="grid-tile"></span><span class="grid-tile"></span>
    <span class="grid-tile"></span><span class="grid-tile"></span><span class="grid-tile"></span><span class="grid-tile"></span><span class="grid-tile"></span><span class="grid-tile"></span><span class="grid-tile"></span><span class="grid-tile"></span>
    <span class="grid-tile"></span><span class="grid-tile"></span><span class="grid-tile"></span><span class="grid-tile"></span><span class="grid-tile"></span><span class="grid-tile"></span><span class="grid-tile"></span><span class="grid-tile"></span>
    <span class="grid-tile"></span><span class="grid-tile"></span><span class="grid-tile"></span><span class="grid-tile"></span><span class="grid-tile"></span><span class="grid-tile"></span><span class="grid-tile"></span><span class="grid-tile"></span>
    <span class="grid-tile"></span><span class="grid-tile"></span><span class="grid-tile"></span><span class="grid-tile"></span><span class="grid-tile"></span><span class="grid-tile"></span><span class="grid-tile"></span><span class="grid-tile"></span>
  </div>
  <div class="foot"><b>LUMEROVA</b> | Copyright © All Rights Reserved</div><div class="pg">17</div>
</section>

<!-- 18 similar names -->
<section class="slide c2" style="top:2711px">
  <div class="brand sm">lumerova</div>
  <div style="position:absolute;left:0;top:148px;width:10px;height:26px;background:var(--magenta)"></div>
  <div style="position:absolute;left:22px;top:142px;font-size:13px;line-height:17px;font-weight:500">Logos From Other<br>Companies With<br>Similar Names</div>
  <div style="position:absolute;left:175px;top:50px;width:385px;height:260px;background:#fff;box-shadow:0 2px 8px rgba(0,0,0,.12)"></div>
  <div class="tile-grid" style="left:188px;top:62px;width:360px;grid-template-columns:repeat(6,1fr);gap:12px 10px">
    <span class="grid-tile"></span><span class="grid-tile"></span><span class="grid-tile"></span><span class="grid-tile"></span><span class="grid-tile"></span><span class="grid-tile"></span>
    <span class="grid-tile"></span><span class="grid-tile"></span><span class="grid-tile"></span><span class="grid-tile"></span><span class="grid-tile"></span><span class="grid-tile"></span>
    <span class="grid-tile"></span><span class="grid-tile"></span><span class="grid-tile"></span><span class="grid-tile"></span><span class="grid-tile"></span><span class="grid-tile"></span>
    <span class="grid-tile"></span><span class="grid-tile"></span><span class="grid-tile"></span><span class="grid-tile"></span><span class="grid-tile"></span><span class="grid-tile"></span>
    <span class="grid-tile"></span><span class="grid-tile"></span><span class="grid-tile"></span><span class="grid-tile"></span><span class="grid-tile"></span><span class="grid-tile"></span>
    <span class="grid-tile"></span><span class="grid-tile"></span><span class="grid-tile"></span><span class="grid-tile"></span><span class="grid-tile"></span><span class="grid-tile"></span>
    <span class="grid-tile"></span><span class="grid-tile"></span><span class="grid-tile"></span><span class="grid-tile"></span><span class="grid-tile"></span><span class="grid-tile"></span>
    <span class="grid-tile"></span><span class="grid-tile"></span><span class="grid-tile"></span><span class="grid-tile"></span><span class="grid-tile"></span><span class="grid-tile"></span>
  </div>
  <div class="foot"><b>LUMEROVA</b> | Copyright © All Rights Reserved</div><div class="pg">18</div>
</section>

<!-- 19 thank you magenta -->
<section class="slide c1" style="top:3048px">
  <div class="photo" role="img" aria-label="Magenta-tinted photo of a team meeting in an office" style="inset:0;background:linear-gradient(135deg,#e2479a,#d01677 55%,#b8136a)"></div>
  <div class="brand white" style="left:0;width:578px;justify-content:center;top:70px;font-size:40px">lumerova</div>
  <div style="position:absolute;left:0;top:218px;width:578px;text-align:center;color:#fff;font-size:20px;font-weight:600">Thank You. <span style="color:#f79bc7">Contact Us.</span></div>
  <div class="contact"><span>www.website.com</span><span>Here to write your Company adress</span><span>(000) 000-0000</span><span>info@website.com</span></div>
  <div class="pg">19</div>
</section>

<!-- 20 thank you black -->
<section class="slide c2" style="top:3048px;background:#141414">
  <div class="brand white" style="left:0;width:578px;justify-content:center;top:70px;font-size:40px">lumerova</div>
  <div style="position:absolute;left:0;top:218px;width:578px;text-align:center;color:#fff;font-size:20px;font-weight:600">Thank You. <span style="color:var(--magenta)">Contact Us.</span></div>
  <div class="contact"><span>www.website.com</span><span>Here to write your Company adress</span><span>(000) 000-0000</span><span>info@website.com</span></div>
  <div class="pg" style="background:none">20</div>
</section>

<!-- 21 palette -->
<section class="slide c1" style="top:3385px">
  <div class="brand sm">lumerova</div>
  <div style="position:absolute;left:36px;top:118px;font-size:13px;font-weight:600;line-height:18px;text-align:center">PRIMARY<br>COLOR</div>
  <div class="swatch-label" style="left:120px">+1</div><div class="swatch-label" style="left:200px">+2</div><div class="swatch-label" style="left:280px">+3</div><div class="swatch-label" style="left:360px">+4</div><div class="swatch-label" style="left:440px">+5</div>
  <div class="swatch" style="left:40px;background:var(--magenta)"></div>
  <div class="swatch" style="left:120px;background:var(--pink)"></div>
  <div class="swatch" style="left:200px;background:var(--plum)"></div>
  <div class="swatch" style="left:280px;background:var(--teal-light)"></div>
  <div class="swatch" style="left:360px;background:var(--teal)"></div>
  <div class="swatch" style="left:440px;background:var(--green)"></div>
  <div class="foot"><b>LUMEROVA</b> | Copyright © All Rights Reserved</div><div class="pg">21</div>
</section>

</body>
</html>
```